interior designer/stylist looking for a letter press business card to reflect the stylish work

Hello Designers,
I need a business card design for an company called Mosaic Interior Design. I'm aiming at the high end residential and private client market in London providing sleek simple interiors. I'd like my business card to be pinterest worthy and expensive looking, i want people to pin it and for it to have a sought after look, and want prospective customers to hire me as their interior designer as my card is so beautiful.
I love letter press design. I also like the use of colour/foil on the edge.
Colour combos & general things I like -
Black and White
Navy Blue and Gold
Neutral colours (muted palette of greys whites navys beiges)
White Marble & brass
Vorelle (fashion designer)
....also open to other suggestions....
Please dont take the pink in the attached photos too literally. i'd like the card to look more masculine than feminine.
I'd like Mosaic on one side in one font, with interior design underneath so one word will make the statement....... unless anyone has any other ideas, open to suggestions.
I'd like a really simple font and for the whole card to look very graphic.
my details -
Petra Wendlecombe
Interior Designer & Stylist
email petra@mosaicinteriordesign.co.uk
phone +447311584209
website wwww.mosaicinteriordesign.co.uk
GO GO GO!! EXCITED TO SEE THE OUTCOME!!
x P
Target Market(s)
High End Residential and private clients
Industry/Entity Type
Business
Contact Information for Business Card
Mosaic Interior Design & Styling
Petra Wendlecombe
phone +447311584209

```html
<!DOCTYPE html>
<html lang="en">
<head>
<meta charset="utf-8">
<title>Mosaic Interior Design – Business Card</title>
<link href="https://fonts.googleapis.com/css2?family=Source+Sans+3:wght@400;600&display=swap" rel="stylesheet">
<style>
  :root {
    --backdrop: #ebe9e6;
    --card-amber: #ffaa00;
    --curve-band: #eea207;
    --curve-deep: #df960c;
    --ink: #1c1a17;
    --sans: "Source Sans 3", sans-serif;
  }
  * { margin: 0; padding: 0; box-sizing: border-box; }
  html, body {
    width: 1200px; height: 900px; overflow: hidden;
    background: var(--backdrop);
  }
  .stage { position: relative; width: 1200px; height: 900px; }

  .card {
    position: absolute;
    background: var(--card-amber);
    overflow: hidden;
    box-shadow: 0 6px 18px rgba(0,0,0,0.12);
    color: var(--ink);
  }
  .card--front { left: 238px; top: 62px; width: 555px; height: 341px; }
  .card--back  { left: 458px; top: 518px; width: 559px; height: 342px; }

  .card__curves { position: absolute; inset: 0; width: 100%; height: 100%; }
  .curve-band { fill: var(--curve-band); }
  .curve-deep { fill: var(--curve-deep); }

  .wordmark {
    position: absolute;
    font-family: var(--sans);
    font-weight: 600;
    color: var(--ink);
    line-height: 1;
    white-space: nowrap;
    letter-spacing: 0.5px;
  }
  .card--front .wordmark { left: 72px; top: 52px; font-size: 28px; }
  .card--back .wordmark { left: 0; right: 0; top: 150px; font-size: 34px; text-align: center; padding-left: 60px; }

  .holder {
    position: absolute; right: 36px; top: 166px;
    text-align: right; font-family: var(--sans);
  }
  .holder__name { font-size: 19px; font-weight: 600; }
  .holder__role { font-size: 14.5px; margin-top: 6px; }

  .contact {
    position: absolute; left: 40px; top: 245px;
    list-style: none; font-family: var(--sans); font-size: 15px;
  }
  .contact__item { display: flex; align-items: center; height: 23px; }
  .contact__icon { width: 11px; height: 11px; margin-right: 7px; fill: var(--ink); }
</style>
</head>
<body>
<main class="stage">

  <section class="card card--front" aria-label="Business card front">
    <svg class="card__curves" viewBox="0 0 555 341" preserveAspectRatio="none" aria-hidden="true">
      <path class="curve-band" d="M24 0 C 90 200, 300 300, 555 341 L0 341 L0 0 Z"/>
      <path class="curve-deep" d="M60 0 C 140 190, 320 290, 548 341 L0 341 L0 0 Z"/>
    </svg>
    <h1 class="wordmark">Mosaic Interior Design</h1>
    <div class="holder">
      <p class="holder__name">Petra Wendlecombe</p>
      <p class="holder__role">Interior Designer &amp; Stylist</p>
    </div>
    <ul class="contact">
      <li class="contact__item">
        <svg class="contact__icon" viewBox="0 0 12 12" aria-hidden="true"><path d="M1 4 C1 2 3 1 6 1 C9 1 11 2 11 4 L8.5 4.5 L8 3 H4 L3.5 4.5 Z M3 6 H9 L10 11 H2 Z"/></svg>
        +447311584209
      </li>
      <li class="contact__item">
        <svg class="contact__icon" viewBox="0 0 12 12" aria-hidden="true"><path d="M1 2.5 H11 V10 H1 Z M1.5 3 L6 7 L10.5 3" stroke="#df960c" stroke-width="0.9"/></svg>
        petra@mosaicinteriordesign.co.uk
      </li>
      <li class="contact__item">
        <svg class="contact__icon" viewBox="0 0 12 12" aria-hidden="true"><g fill="none" stroke="#1c1a17" stroke-width="1.4"><rect x="1" y="5.5" width="5.5" height="3.5" rx="1.7" transform="rotate(-45 3.75 7.25)"/><rect x="5.5" y="3" width="5.5" height="3.5" rx="1.7" transform="rotate(-45 8.25 4.75)"/></g></svg>
        wwww.mosaicinteriordesign.co.uk
      </li>
    </ul>
  </section>

  <section class="card card--back" aria-label="Business card back">
    <svg class="card__curves" viewBox="0 0 559 342" preserveAspectRatio="none" aria-hidden="true">
      <path class="curve-band" d="M10 0 C 80 210, 310 305, 559 342 L0 342 L0 0 Z"/>
      <path class="curve-deep" d="M36 0 C 120 215, 330 305, 552 342 L0 342 L0 0 Z"/>
    </svg>
    <h2 class="wordmark">Mosaic Interior Design</h2>
  </section>

</main>
</body>
</html>
```